The design should look similar to the uploaded example to accommodate the information needed for a business card template. I would like to see the colors orange and charcoal grey incorporated along with the logo.The following should be on the back of the card SPECIALIZING IN NEW AND USED TIRES & WHEELS FOR:- Loaders- Skid Steers- Telehandlers- Boom Lifts- Forklifs and moreELIMINATING DOWNTIMEWheel Exchange Program for New & Used Foam Filled and Solid Rubber TiresSPECIALTY SERVICES- Foam Filling Tires- Largest Tire Press in SE- ONSITE Forklift Tire Press- Boom Truck Services - Rubber Tracks

Target Market(s)

New and Existing Customers

Industry/Entity Type

Business

Contact Information for Business Card

NAMEHEAVY DUTY TIRE, LLC8470 Belvedere RoadWest Palm Beach, FL 33411P: 844-HD-TIRESF: 561-431-6469C:E: W: WWW.GRANITERIMSUPPLY-EXAMPLE.COM

Font styles to use
Sans Serif

Colors
f37122
333333

Requirements
Must have
• The logo and the information indicated for the backside of the card
Nice to have
• Keep the orange and charcoal grey colors

```html
<!DOCTYPE html>
<html lang="en">
<head>
<meta charset="utf-8">
<title>Granite Rim Supply, LLC – Business Card</title>
<link rel="stylesheet" href="https://fonts.googleapis.com/css2?family=Arvo:wght@700&family=Open+Sans:ital,wght@0,400;0,600;1,400&display=swap">
<style>
  :root {
    --orange: #e0722f;
    --charcoal: #333c3d;
    --paper: #f4f4f2;
    --ink: #4a4a4a;
    --backdrop: #8f9090;
    --white: #ffffff;
  }
  * { box-sizing: border-box; margin: 0; padding: 0; }
  html, body { width: 1105px; height: 1200px; overflow: hidden; }
  body { background: var(--backdrop); font-family: "Open Sans", Arial, sans-serif; position: relative; }

  .card { position: absolute; left: 182px; width: 747px; height: 427px; overflow: hidden; }
  .card--front { top: 119px; background: var(--paper); }
  .card--back { top: 637px; background: var(--orange); color: var(--white); }

  /* Front */
  .brand-mark { position: absolute; left: 163px; top: 61px; width: 124px; height: 124px; border-radius: 50%; background: var(--charcoal); }
  .brand-name { position: absolute; left: 296px; top: 86px; font-family: "Arvo", Georgia, serif; font-weight: 700; font-size: 33px; line-height: 38px; color: var(--charcoal); letter-spacing: 0.5px; }
  .accent-bar { position: absolute; }
  .accent-bar--left { left: 0; top: 247px; width: 15px; height: 135px; background: var(--orange); }
  .accent-bar--right { right: 0; top: 261px; width: 17px; height: 115px; background: var(--charcoal); }

  .contact-list { position: absolute; left: 50px; top: 243px; list-style: none; }
  .contact-list li { display: flex; align-items: center; height: 28.5px; font-size: 19.5px; color: var(--ink); }
  .contact-list svg { width: 18px; height: 18px; margin-right: 12px; fill: var(--charcoal); flex: none; }

  .person { position: absolute; right: 50px; top: 258px; text-align: right; }
  .person-name { font-family: "Arvo", Georgia, serif; font-weight: 700; font-size: 27px; color: var(--charcoal); letter-spacing: 0.5px; line-height: 34px; }
  .person-role { font-family: "Arvo", Georgia, serif; font-weight: 700; font-size: 19px; color: var(--orange); line-height: 26px; letter-spacing: 0.5px; }
  .person-address { margin-top: 12px; font-size: 19.5px; line-height: 28px; color: var(--ink); }

  /* Back */
  .back-emblem { position: absolute; left: -27px; top: 23px; width: 380px; height: 380px; border-radius: 50%; background: var(--charcoal); }
  .services { position: absolute; right: 35px; top: 36px; text-align: right; }
  .services h2 { font-weight: 600; font-size: 19.5px; line-height: 27px; letter-spacing: 0.2px; }
  .services p { font-size: 19px; line-height: 26px; }
  .services .items { font-style: italic; font-size: 19px; line-height: 27px; }
  .services .group + .group { margin-top: 14px; }
  .dot { display: inline-block; width: 7px; height: 7px; border-radius: 50%; background: var(--white); margin: 0 6px 3px 6px; vertical-align: middle; }
</style>
</head>
<body>

<section class="card card--front" aria-label="Business card front">
  <div class="brand-mark" aria-hidden="true"></div>
  <div class="brand-name">GRANITE RIM<br>SUPPLY LLC</div>

  <div class="accent-bar accent-bar--left"></div>
  <ul class="contact-list">
    <li><svg viewBox="0 0 24 24"><path d="M6.6 10.8a15.1 15.1 0 0 0 6.6 6.6l2.2-2.2c.3-.3.7-.4 1-.2 1.1.4 2.3.6 3.6.6.6 0 1 .4 1 1V20c0 .6-.4 1-1 1A17 17 0 0 1 3 4c0-.6.4-1 1-1h3.5c.6 0 1 .4 1 1 0 1.3.2 2.5.6 3.6.1.3 0 .7-.2 1z"/></svg>844-GR-WHEEL</li>
    <li><svg viewBox="0 0 24 24"><path d="M7 1h10a2 2 0 0 1 2 2v18a2 2 0 0 1-2 2H7a2 2 0 0 1-2-2V3a2 2 0 0 1 2-2zm0 3v14h10V4zm5 15.5a1.2 1.2 0 1 0 0 2.4 1.2 1.2 0 0 0 0-2.4z"/></svg>836 512 7740</li>
    <li><svg viewBox="0 0 24 24"><path d="M6 2h12v5H6zM4 8h16a2 2 0 0 1 2 2v7h-4v5H6v-5H2v-7a2 2 0 0 1 2-2zm4 7v5h8v-5z"/></svg>561-278-9053</li>
    <li><svg viewBox="0 0 24 24"><path d="M2 5h20v2l-10 6L2 7zm0 4.3 10 6 10-6V19H2z"/></svg>info@graniterim-example.com</li>
    <li><svg viewBox="0 0 24 24"><path d="M12 2a10 10 0 1 0 0 20 10 10 0 0 0 0-20zm-1 17.9A8 8 0 0 1 4.2 10.2L9 15v1a2 2 0 0 0 2 2zm6.9-2.5A2 2 0 0 0 16 16h-1v-3a1 1 0 0 0-1-1H8v-2h2a1 1 0 0 0 1-1V7h2a2 2 0 0 0 2-2v-.4a8 8 0 0 1 2.9 12.8z"/></svg>www.graniterimsupply-example.com</li>
  </ul>

  <div class="person">
    <div class="person-name">DANIEL REYES</div>
    <div class="person-role">CEO/FOUNDER</div>
    <div class="person-address">5126 Marston Lane<br>Lakeview Springs, FL 33499</div>
  </div>
  <div class="accent-bar accent-bar--right"></div>
</section>

<section class="card card--back" aria-label="Business card back">
  <div class="back-emblem" aria-hidden="true"></div>
  <div class="services">
    <div class="group">
      <h2>SPECIALIZING IN NEW AND</h2>
      <h2>USED TIRES &amp; WHEELS FOR</h2>
      <div class="items">Loaders<span class="dot"></span>Skid Steers<span class="dot"></span>Telehandlers<span class="dot"></span></div>
      <div class="items">Boom Lifts<span class="dot"></span>Forklifs and more<span class="dot"></span></div>
    </div>
    <div class="group">
      <h2>ELIMINATING DOWNTIME</h2>
      <p>Wheel Exchange Program for New &amp;</p>
      <p>Used Foam Filled &amp; Solid Rubber Tires</p>
    </div>
    <div class="group">
      <h2>SPECIALTY SERVICES</h2>
      <div class="items">Foam Filling Tires<span class="dot"></span></div>
      <div class="items">Largest Tire Press in SE<span class="dot"></span></div>
      <div class="items">ONSITE Forklift Tire Press<span class="dot"></span></div>
      <div class="items">Boom Truck Services<span class="dot"></span>Rubber Tracks<span class="dot"></span></div>
    </div>
  </div>
</section>

</body>
</html>
```